Website Redesign using existing images, copy etc.

I'm looking for a website redesign/refresh of my current WordPress website. I would like to utilize the same photography, a new photo viewer, and an overall refresh of the entire design. This will need to be WordPress with simple accessibility to make changes as we add additional properties and make updates. We auction luxury real estate and luxury yachts for non-distressed sellers. It needs to be simple, luxurious and with ease of use for both web and especially mobile. www.BrindleHarrow.com

```html
<!DOCTYPE html>
<html lang="en">
<head>
<meta charset="utf-8">
<title>Brindle Harrow — Real Estate &amp; Yachts</title>
<link href="https://fonts.googleapis.com/css2?family=Cinzel:wght@400;600;700&family=Lato:wght@400;700&display=swap" rel="stylesheet">
<style>
:root{
  --gold:#8e7d5f;
  --gold-light:#b9a67f;
  --tan-panel:#9c8b6c;
  --ink:#1b1b1b;
  --dark:#151515;
  --text:#4a4a4a;
  --white:#ffffff;
  --soft:#f3f1ec;
}
*{box-sizing:border-box;margin:0;padding:0}
html,body{width:1200px;height:3872px;overflow:hidden;background:var(--white)}
body{font-family:'Lato',sans-serif;color:var(--text);position:relative}
.page{position:relative;width:1200px;height:3872px;overflow:hidden}
.serif{font-family:'Cinzel',serif}
.abs{position:absolute}

/* nav */
.site-nav{position:absolute;top:0;left:0;width:1200px;height:84px;background:rgba(10,20,35,.35);display:flex;align-items:center;justify-content:space-between;padding:0 120px 0 120px;z-index:3}
.brand{display:flex;align-items:center;gap:10px;color:var(--white);font-family:'Cinzel',serif;font-size:22px;letter-spacing:3px;font-weight:600}
.brand-dot{width:20px;height:20px;border-radius:50%;border:2px solid var(--white)}
.nav-links{display:flex;gap:34px;list-style:none;font-family:'Cinzel',serif;font-size:14px;font-weight:700;letter-spacing:1px;color:var(--white)}
.nav-phone{color:var(--gold-light)}

/* hero */
.hero{position:absolute;top:0;left:0;width:1200px;height:660px;background:linear-gradient(180deg,#1e3a5a 0%,#2d5a7d 35%,#1f4058 60%,#0f2130 100%)}
.hero-title{position:absolute;top:340px;width:100%;text-align:center;color:var(--white);font-family:'Cinzel',serif;font-size:60px;line-height:64px;font-weight:600;letter-spacing:3px}
.hero-sub{position:absolute;top:482px;width:100%;text-align:center;color:var(--gold-light);font-family:'Cinzel',serif;font-size:24px;letter-spacing:3px;font-weight:600}
.hero-actions{position:absolute;top:530px;width:100%;display:flex;justify-content:center;gap:30px}
.pill{display:inline-flex;align-items:center;gap:14px;height:44px;padding:0 6px 0 24px;border-radius:22px;font-family:'Cinzel',serif;font-weight:700;font-size:13px;letter-spacing:1.5px}
.pill-light{background:var(--white);color:var(--ink)}
.pill-ghost{border:2px solid var(--white);color:var(--white)}
.pill-gold{background:var(--gold);color:var(--white)}
.pill-arrow{width:32px;height:32px;border-radius:50%;background:var(--gold);display:flex;align-items:center;justify-content:center}
.pill-gold .pill-arrow,.pill-ghost .pill-arrow{background:var(--white)}
.hero-dots{position:absolute;top:606px;width:100%;display:flex;justify-content:center;gap:10px}
.hero-dots span{width:10px;height:10px;border-radius:50%;background:rgba(255,255,255,.5)}
.hero-dots span:first-child{background:var(--white)}

/* about */
.about-media{position:absolute;left:560px;top:760px;width:530px;height:660px;border-radius:70px 0 70px 0;background:linear-gradient(180deg,#a9cbe6 0%,#7fb0d6 45%,#e9eef2 60%,#3c6f93 100%)}
.about-card{position:absolute;left:168px;top:820px;width:514px;height:670px;background:var(--white);box-shadow:0 10px 40px rgba(0,0,0,.16);padding:44px 46px}
.section-title{font-family:'Cinzel',serif;color:var(--gold);font-size:30px;letter-spacing:2px;font-weight:600}
.section-title b{color:var(--ink);font-weight:600}
.about-card .section-title{text-align:center}
.rule{width:60px;height:2px;background:var(--gold);margin:10px auto 26px}
.founder{display:flex;gap:26px;align-items:flex-start}
.founder-photo{width:118px;height:130px;background:linear-gradient(180deg,#8f9aa6,#4e5a66)}
.founder-name{font-family:'Cinzel',serif;color:var(--ink);font-size:17px;font-weight:700;letter-spacing:1px;margin-top:10px}
.founder-role{font-family:'Cinzel',serif;font-size:12px;letter-spacing:1px;margin-top:6px;color:var(--text)}
.about-copy{font-size:15px;line-height:27px;margin:24px 0 26px}

/* billion band */
.billion{position:absolute;top:1520px;left:0;width:1200px;height:390px;background:linear-gradient(180deg,#2a2622,#14120f)}
.billion svg{position:absolute;left:0;width:1200px}
.billion-title{position:absolute;top:130px;width:100%;text-align:center;color:var(--white);font-family:'Cinzel',serif;font-size:30px;letter-spacing:2px;font-weight:600}
.billion-sub{position:absolute;top:178px;width:100%;text-align:center;color:var(--white);font-family:'Cinzel',serif;font-size:18px;letter-spacing:2px}
.billion-copy{position:absolute;top:222px;left:110px;width:980px;text-align:center;color:#d8d3c8;font-size:14px;line-height:24px}

/* featured */
.featured{position:absolute;top:2000px;left:0;width:1200px;text-align:center}
.featured .section-title{font-size:30px}
.featured-copy{width:980px;margin:18px auto 0;font-size:14px;line-height:24px}
.badges{display:flex;justify-content:center;gap:28px;margin-top:32px}
.badge{width:164px;height:78px;background:var(--white);border-radius:12px;box-shadow:0 6px 20px rgba(0,0,0,.12);display:flex;align-items:center;justify-content:center}
.badge i{display:block;width:96px;height:26px;border-radius:4px;background:#cfcac0}
.featured .pill{margin-top:34px}

/* sold */
.sold-photo{position:absolute;top:2400px;left:0;width:660px;height:680px;background:linear-gradient(160deg,#d9d6cf 0%,#b9b4aa 45%,#6d6a64 100%)}
.sold-panel{position:absolute;top:2400px;left:660px;width:540px;height:680px;background:var(--tan-panel);padding:150px 60px 0 60px;color:var(--white)}
.sold-panel h2{font-family:'Cinzel',serif;font-size:28px;letter-spacing:2px;font-weight:600}
.sold-panel p{font-size:15px;line-height:28px;margin-top:24px;color:#f4efe5}

/* cta */
.cta-strip{position:absolute;top:3250px;left:180px;width:840px;height:190px;background:linear-gradient(90deg,#cfd6d6,#9fb0b2 50%,#d7dcd8)}
.cta-actions{position:absolute;top:3275px;left:0;width:1200px;display:flex;flex-direction:column;align-items:center;gap:14px}

/* footer */
.site-footer{position:absolute;top:3496px;left:0;width:1200px;height:376px;background:var(--dark);color:var(--white)}
.footer-cols{position:absolute;top:52px;left:120px;display:flex;gap:90px}
.footer-cols h4{font-family:'Cinzel',serif;font-size:14px;letter-spacing:1.5px;font-weight:700;margin-bottom:18px}
.footer-cols ul{list-style:none;font-size:14px;line-height:30px;color:#d3d0ca}
.social{display:flex;gap:10px}
.social span{width:28px;height:28px;border-radius:50%;background:var(--white)}
.social-seal{width:64px;height:64px;border-radius:50%;background:#3a3833;margin:22px 0 0 42px}
.signup input{display:block;width:220px;height:28px;border:none;border-radius:3px;margin-bottom:10px;padding:0 10px;font-family:'Lato',sans-serif;font-size:13px}
.signup input:first-child{background:var(--gold-light)}
.signup .pill{height:30px;font-size:11px;padding:0 4px 0 16px;background:var(--white);color:var(--ink)}
.signup .pill-arrow{width:22px;height:22px}
.footer-bottom{position:absolute;bottom:24px;width:100%;text-align:center;font-size:13px;color:#bdb9b0}
.footer-top-link{position:absolute;right:20px;bottom:90px;font-size:11px;color:#bdb9b0}
</style>
</head>
<body>
<div class="page">

  <header class="hero" role="img" aria-label="Evening view of a luxury waterfront resort with palms and a lit pool"></header>
  <nav class="site-nav">
    <div class="brand"><span class="brand-dot"></span>BRINDLE HARROW</div>
    <ul class="nav-links">
      <li>BUY</li><li>SELL</li><li>ABOUT</li><li>CONTACT</li><li class="nav-phone">800-555-0142</li>
    </ul>
  </nav>
  <h1 class="hero-title">WELCOME TO<br>BRINDLE HARROW</h1>
  <p class="hero-sub">REAL ESTATE &amp; YACHTS</p>
  <div class="hero-actions">
    <span class="pill pill-light">BROWSE UPCOMING <span class="pill-arrow"><svg width="14" height="14" viewBox="0 0 14 14"><path d="M2 7h10M8 3l4 4-4 4" stroke="#fff" stroke-width="2" fill="none"/></svg></span></span>
    <span class="pill pill-ghost">BROWSE PAST AUCTIONS <span class="pill-arrow"><svg width="14" height="14" viewBox="0 0 14 14"><path d="M2 7h10M8 3l4 4-4 4" stroke="#8e7d5f" stroke-width="2" fill="none"/></svg></span></span>
  </div>
  <div class="hero-dots"><span></span><span></span></div>

  <section>
    <div class="about-media" role="img" aria-label="Luxury motor yacht at sea under a blue sky"></div>
    <article class="about-card">
      <h2 class="section-title">ABOUT <b>US</b></h2>
      <div class="rule"></div>
      <div class="founder">
        <div class="founder-photo" role="img" aria-label="Portrait of the founder"></div>
        <div>
          <p class="founder-name">MILES CORBETT</p>
          <p class="founder-role">CEO &amp; FOUNDER</p>
        </div>
      </div>
      <p class="about-copy">Have you ever experienced a sense of purpose in your life? I consider myself fortunate enough to have felt it more than once. Early on I found my first calling in sales, and I enjoyed every year of it. Later I discovered auctions, and I knew at once this was the path I wanted to follow for the rest of my career.</p>
      <span class="pill pill-gold">READ MORE <span class="pill-arrow"><svg width="14" height="14" viewBox="0 0 14 14"><path d="M2 7h10M8 3l4 4-4 4" stroke="#8e7d5f" stroke-width="2" fill="none"/></svg></span></span>
    </article>
  </section>

  <section class="billion" role="img" aria-label="Dark panoramic view of a luxury home at dusk">
    <svg style="top:0" height="40" viewBox="0 0 1200 40" preserveAspectRatio="none"><path d="M0 0H1200V8Q600 60 0 8Z" fill="#fff"/></svg>
    <h2 class="billion-title">OVER ONE BILLION DOLLARS OF AUCTIONS MARKETED</h2>
    <p class="billion-sub">REAL ESTATE &amp; YACHTS</p>
    <p class="billion-copy">The experience of hearing the auctioneer's final proclamation of SOLD is unparalleled. Whether you are a buyer or a seller, every auction we market brings together the right audience, a clear timeline and the certainty of a closing date you can plan around.</p>
    <svg style="bottom:0" height="40" viewBox="0 0 1200 40" preserveAspectRatio="none"><path d="M0 40H1200V32Q600 -20 0 32Z" fill="#fff"/></svg>
  </section>

  <section class="featured">
    <h2 class="section-title"><b>AS</b> FEATURED IN</h2>
    <p class="featured-copy">By offering superior properties and results globally, along with strategic auction dates and exceptional marketing, our sales have been covered by the most prominent media outlets. Here are some of our favorite press features.</p>
    <div class="badges">
      <div class="badge"><i></i></div><div class="badge"><i></i></div><div class="badge"><i></i></div><div class="badge"><i></i></div><div class="badge"><i></i></div>
    </div>
    <span class="pill pill-gold">VIEW PRESS <span class="pill-arrow"><svg width="14" height="14" viewBox="0 0 14 14"><path d="M2 7h10M8 3l4 4-4 4" stroke="#8e7d5f" stroke-width="2" fill="none"/></svg></span></span>
  </section>

  <section>
    <div class="sold-photo" role="img" aria-label="Bright modern living room with fireplace and built-in shelving"></div>
    <div class="sold-panel">
      <h2>SOLD BY BRINDLE HARROW</h2>
      <p>Brindle Harrow is a top-tier destination for luxury property auctions, having overseen the accelerated marketing of numerous high-end homes and yachts. Our team of luxury home auction experts is committed to helping property owners obtain the best value for their assets while ensuring a smooth sale. Whether you own a waterfront estate or a motor yacht, we bring the audience, the photography, the cinematography and the campaign needed to reach qualified buyers. We run every auction with care, clarity and a firm timeline from first call to closing.</p>
    </div>
  </section>

  <section>
    <div class="cta-strip" role="img" aria-label="Soft coastal landscape backdrop"></div>
    <div class="cta-actions">
      <span class="pill pill-light">LEARN ABOUT US <span class="pill-arrow"><svg width="14" height="14" viewBox="0 0 14 14"><path d="M2 7h10M8 3l4 4-4 4" stroke="#fff" stroke-width="2" fill="none"/></svg></span></span>
      <span class="pill pill-light">BROWSE UPCOMING AUCTIONS <span class="pill-arrow"><svg width="14" height="14" viewBox="0 0 14 14"><path d="M2 7h10M8 3l4 4-4 4" stroke="#fff" stroke-width="2" fill="none"/></svg></span></span>
    </div>
  </section>

  <footer class="site-footer">
    <div class="footer-cols">
      <div><h4>QUICK LINK</h4><ul><li>Home</li><li>Buy</li><li>Sell</li><li>About</li><li>Blog</li><li>Contact</li></ul></div>
      <div><h4>OTHER LINK</h4><ul><li>Terms Of Service</li><li>Privacy Policy</li><li>Copyright Policy</li></ul></div>
      <div><h4>FOLLOW ALONG</h4><div class="social"><span></span><span></span><span></span><span></span></div><div class="social-seal"></div></div>
      <div class="signup"><h4>SIGNUP FOR BRINDLE ALERTS</h4><input type="text" placeholder="Name"><input type="text" placeholder="Email"><span class="pill">SUBMIT <span class="pill-arrow"><svg width="12" height="12" viewBox="0 0 14 14"><path d="M2 7h10M8 3l4 4-4 4" stroke="#fff" stroke-width="2" fill="none"/></svg></span></span></div>
    </div>
    <span class="footer-top-link">TOP</span>
    <p class="footer-bottom">© Copyright 2023 BRINDLE HARROW . All Rights Reserved.</p>
  </footer>

</div>
</body>
</html>
```